MARLOW FENN - business card
A way to remember us and buy our products
Professional
MARLOWFENN - the loyal pick
Hagbergsv. 27
SE-712 43 Eskilstuna
SWEDEN
info@marlowfenn-demo.se
www.marlowfenn-demo.se
I would like the business cards and other material to match.
It is about dogs and our show trolley.
I need something to hand out as I meet people at dog shows or otherwise.
your ideas are welcome to figure out what the backside should be.
drawing of product_logo related
LOGO in whole, van be split into two
4 berth
LOGO PDF
drawing pdf
Product today. Steel 2 berth

```html
<!DOCTYPE html>
<html lang="en">
<head>
<meta charset="utf-8">
<title>MARLOW FENN - business card</title>
<link rel="stylesheet" href="https://fonts.googleapis.com/css2?family=Open+Sans:wght@400;600;700&display=swap">
<style>
  :root {
    --bg: #e9e6e1;
    --card: #ffffff;
    --orange: #ef7d1a;
    --blue: #1f4f8f;
    --grey: #6b6f75;
    --soft: #f6e6d2;
    --shadow: rgba(0, 0, 0, 0.14);
  }
  * { box-sizing: border-box; margin: 0; padding: 0; }
  html, body { width: 1200px; height: 646px; overflow: hidden; }
  body {
    background: var(--bg);
    font-family: "Open Sans", Arial, sans-serif;
    position: relative;
  }
  .card {
    position: absolute;
    top: 168px;
    width: 540px;
    height: 309px;
    background: var(--card);
    box-shadow: 0 6px 18px var(--shadow);
    overflow: hidden;
  }
  .card--front { left: 40px; }
  .card--back { left: 620px; }

  /* Front */
  .dog-decoration {
    position: absolute;
    right: -10px;
    top: 30px;
    width: 220px;
    height: 250px;
    border-radius: 48% 52% 40% 60%;
    background: radial-gradient(circle at 45% 45%, var(--soft), rgba(246, 230, 210, 0) 72%);
  }
  .brand {
    position: absolute;
    left: 40px;
    top: 42px;
    display: flex;
    align-items: center;
    gap: 12px;
  }
  .brand__mark {
    width: 30px;
    height: 30px;
    border-radius: 50%;
    background: var(--blue);
  }
  .brand__name {
    font-size: 40px;
    font-weight: 700;
    color: var(--orange);
    letter-spacing: 0.5px;
    line-height: 1;
  }
  .tagline {
    position: absolute;
    left: 82px;
    top: 90px;
    font-size: 12px;
    color: var(--grey);
  }
  .person {
    position: absolute;
    left: 40px;
    top: 158px;
  }
  .person__name {
    font-size: 15px;
    font-weight: 700;
    color: var(--blue);
    margin-bottom: 8px;
  }
  .contact { list-style: none; }
  .contact__line {
    display: flex;
    align-items: center;
    gap: 8px;
    font-size: 10.5px;
    color: var(--grey);
    line-height: 17px;
  }
  .contact__line--plain { padding-left: 22px; }
  .contact__icon { width: 14px; height: 14px; flex: none; }

  /* Back */
  .back-brand {
    position: absolute;
    left: 0; right: 0;
    top: 100px;
    display: flex;
    flex-direction: column;
    align-items: center;
    gap: 14px;
  }
  .back-brand__mark {
    width: 70px;
    height: 70px;
    background: var(--blue);
    border-radius: 6px;
  }
  .back-brand__name {
    font-size: 22px;
    font-weight: 700;
    color: var(--orange);
    letter-spacing: 0.5px;
  }
  .back-web {
    position: absolute;
    left: 0; right: 0;
    bottom: 40px;
    text-align: center;
    font-size: 10.5px;
    color: var(--grey);
  }
</style>
</head>
<body>
  <section class="card card--front">
    <div class="dog-decoration" role="img" aria-label="Faint dog silhouette decoration"></div>

    <div class="brand">
      <span class="brand__mark"></span>
      <span class="brand__name">MARLOWFENN</span>
    </div>
    <p class="tagline">A way to remember us and buy our products</p>

    <div class="person">
      <p class="person__name">Your Name</p>
      <ul class="contact">
        <li class="contact__line">
          <svg class="contact__icon" viewBox="0 0 14 14"><circle cx="7" cy="7" r="7" fill="#1f4f8f"/><path d="M7 3a2.4 2.4 0 0 0-2.4 2.4C4.6 7.3 7 11 7 11s2.4-3.7 2.4-5.6A2.4 2.4 0 0 0 7 3z" fill="#fff"/><circle cx="7" cy="5.4" r="0.9" fill="#1f4f8f"/></svg>
          Hagbergsv. 27
        </li>
        <li class="contact__line contact__line--plain">SE-712 43 Norrvik, SWEDEN</li>
        <li class="contact__line">
          <svg class="contact__icon" viewBox="0 0 14 14"><circle cx="7" cy="7" r="7" fill="#1f4f8f"/><path d="M4.6 3.6l1.4-.2.8 1.8-.9.7a5 5 0 0 0 2.2 2.2l.7-.9 1.8.8-.2 1.4c-3.3.3-6.1-2.5-5.8-5.8z" fill="#fff"/></svg>
          +46 70 555 01 23
        </li>
        <li class="contact__line">
          <svg class="contact__icon" viewBox="0 0 14 14"><circle cx="7" cy="7" r="7" fill="#1f4f8f"/><rect x="3.5" y="4.5" width="7" height="5" fill="#fff"/><path d="M3.5 4.5L7 7.3l3.5-2.8" fill="none" stroke="#1f4f8f" stroke-width="0.8"/></svg>
          info@marlowfenn-demo.se
        </li>
        <li class="contact__line">
          <svg class="contact__icon" viewBox="0 0 14 14"><circle cx="7" cy="7" r="7" fill="#1f4f8f"/><circle cx="7" cy="7" r="3.6" fill="none" stroke="#fff" stroke-width="0.9"/><path d="M3.4 7h7.2M7 3.4c-1.6 2-1.6 5.2 0 7.2M7 3.4c1.6 2 1.6 5.2 0 7.2" fill="none" stroke="#fff" stroke-width="0.8"/></svg>
          www.marlowfenn-demo.se
        </li>
      </ul>
    </div>
  </section>

  <section class="card card--back">
    <div class="back-brand">
      <span class="back-brand__mark"></span>
      <span class="back-brand__name">MARLOWFENN</span>
    </div>
    <p class="back-web">www.marlowfenn-demo.se</p>
  </section>
</body>
</html>
```